Business Card Design for Property Development Company Director

I am looking for a professional and unforgettable business card design for our Director of our Property Development Company.
Please see attached .pptx file to find out what information to include. You don't have to follow the exact format shown in the file - I am interested to see your creative flair using the information provided.

```html
<!DOCTYPE html>
<html lang="en">
<head>
<meta charset="utf-8">
<title>Harwell Property Group — Business Card</title>
<link href="https://fonts.googleapis.com/css2?family=Arimo:wght@400;700&family=Roboto:wght@400;500&family=Roboto+Condensed:wght@700&display=swap" rel="stylesheet">
<style>
  :root {
    --backdrop: #e4e5e7;
    --brand-blue: #284a8e;
    --brand-blue-dark: #213f7c;
    --ink: #4a4a4c;
    --ink-soft: #6a6a6d;
    --paper: #f3f3f3;
    --rule: #b9babd;
    --white: #ffffff;
  }
  * { margin: 0; padding: 0; box-sizing: border-box; }
  html, body { width: 1200px; height: 726px; overflow: hidden; }
  body {
    background: var(--backdrop);
    font-family: "Arimo", Arial, sans-serif;
    position: relative;
  }
  .card {
    position: absolute;
    top: 213px;
    width: 520px;
    height: 300px;
    border-radius: 3px;
    box-shadow: 0 6px 18px rgba(0,0,0,0.14);
    overflow: hidden;
  }

  /* Front */
  .card-front {
    left: 50px;
    background: var(--brand-blue);
    color: var(--white);
    text-align: center;
    padding-top: 46px;
  }
  .tagline {
    font-size: 19px;
    line-height: 1.2;
    font-weight: 400;
  }
  .front-brand {
    margin-top: 38px;
    display: flex;
    align-items: center;
    justify-content: center;
    gap: 14px;
  }
  .brand-square {
    width: 34px;
    height: 34px;
    background: var(--white);
  }
  .front-brand .brand-name {
    font-size: 34px;
    font-weight: 700;
    letter-spacing: 1px;
    text-align: left;
    line-height: 1;
  }
  .front-brand .brand-name span { display: block; font-size: 15px; letter-spacing: 4px; margin-top: 4px; }
  .invite {
    position: absolute;
    left: 0; right: 0; bottom: 40px;
    font-size: 15px;
  }

  /* Back */
  .card-back {
    left: 630px;
    background: var(--paper);
  }
  .back-band {
    position: absolute;
    left: 0; top: 0; bottom: 0;
    width: 62px;
    background: var(--brand-blue-dark);
  }
  .back-rule {
    position: absolute;
    left: 70px; top: 10px; bottom: 10px;
    width: 1px;
    background: var(--rule);
  }
  .back-content {
    position: absolute;
    left: 100px; top: 34px; right: 24px;
  }
  .back-brand {
    display: flex;
    align-items: center;
    gap: 10px;
    color: var(--ink);
  }
  .back-brand .brand-square { width: 26px; height: 26px; background: var(--ink); }
  .back-brand .brand-name {
    font-size: 27px;
    font-weight: 700;
    letter-spacing: 1px;
    line-height: 1;
  }
  .back-brand .brand-name span { display: block; font-size: 12px; letter-spacing: 3px; margin-top: 3px; }
  .person-name {
    margin-top: 40px;
    font-family: "Roboto Condensed", "Arial Narrow", sans-serif;
    font-weight: 700;
    font-size: 19px;
    color: var(--brand-blue);
  }
  .person-role {
    font-family: "Roboto", Arial, sans-serif;
    font-size: 12px;
    color: var(--ink-soft);
    margin-top: 3px;
  }
  .contact-list {
    list-style: none;
    margin-top: 16px;
    font-family: "Roboto", Arial, sans-serif;
    font-size: 14px;
    color: var(--ink);
  }
  .contact-list li {
    display: flex;
    align-items: center;
    gap: 10px;
    height: 21px;
  }
  .contact-list svg { width: 13px; height: 13px; fill: var(--brand-blue); flex: none; }
  .licence { margin-top: 4px; }
  .licence b { font-weight: 400; color: var(--brand-blue); }
</style>
</head>
<body>

<section class="card card-front" aria-label="Card front">
  <p class="tagline">Property Development<br>&amp; Site Acquisition Specialists</p>
  <div class="front-brand">
    <div class="brand-square"></div>
    <p class="brand-name">HARWELL<span>PROPERTY GROUP</span></p>
  </div>
  <p class="invite">Ask me about our INVESTMENT &amp; PARTNERSHIP opportunities</p>
</section>

<section class="card card-back" aria-label="Card back">
  <div class="back-band"></div>
  <div class="back-rule"></div>
  <div class="back-content">
    <div class="back-brand">
      <div class="brand-square"></div>
      <p class="brand-name">HARWELL<span>PROPERTY GROUP</span></p>
    </div>
    <h1 class="person-name">Daniel Ashford</h1>
    <p class="person-role">Director</p>
    <ul class="contact-list">
      <li>
        <svg viewBox="0 0 24 24" aria-hidden="true"><path d="M6.6 10.8a15.1 15.1 0 0 0 6.6 6.6l2.2-2.2c.3-.3.7-.4 1-.2 1.1.4 2.3.6 3.6.6.6 0 1 .4 1 1V20c0 .6-.4 1-1 1A17 17 0 0 1 3 4c0-.6.4-1 1-1h3.5c.6 0 1 .4 1 1 0 1.3.2 2.5.6 3.6.1.3 0 .7-.2 1z"/></svg>
        0400 218 376
      </li>
      <li>
        <svg viewBox="0 0 24 24" aria-hidden="true"><path d="M2 5h20v14H2zm2 2v.5l8 5 8-5V7zm0 2.8V17h16V9.8l-8 5z"/></svg>
        daniel@harwellpg.com.au
      </li>
      <li>
        <svg viewBox="0 0 24 24" aria-hidden="true"><path d="M12 2a10 10 0 1 0 0 20 10 10 0 0 0 0-20zm6.9 6h-3a15 15 0 0 0-1.3-4A8 8 0 0 1 18.9 8zM12 4c.8 1.2 1.5 2.5 1.9 4h-3.8c.4-1.5 1.1-2.8 1.9-4zM4.3 14a8 8 0 0 1 0-4h3.4a16 16 0 0 0 0 4zm.8 2h3a15 15 0 0 0 1.3 4A8 8 0 0 1 5.1 16zm3-8h-3a8 8 0 0 1 4.3-4c-.6 1.2-1 2.6-1.3 4zM12 20c-.8-1.2-1.5-2.5-1.9-4h3.8c-.4 1.5-1.1 2.8-1.9 4zm2.3-6H9.7a14 14 0 0 1 0-4h4.6a14 14 0 0 1 0 4zm.3 6c.6-1.2 1-2.6 1.3-4h3a8 8 0 0 1-4.3 4zm1.7-6a16 16 0 0 0 0-4h3.4a8 8 0 0 1 0 4z"/></svg>
        www.harwellpg.com.au
      </li>
      <li class="licence">Real Estate Lic: <b>5127340 &amp; 5127341</b></li>
    </ul>
  </div>
</section>

</body>
</html>
```